A new presentation to our clients

we are a Real Estate agency, our website is www.lumibrasa.com and it’s time to have a new, fashion and remarcable Business Card. we want to differentiate ourselves from other companies so we want a business card that differentiates us. we want the business card to impact our customers. in the competitive market that we have today, we have to be different and it is this difference that we seek

Target Market(s)

Real Estate Clients

Contact Information for Business Card

We search a totaly diferent card from the usual

Font styles to use
Sans Serif

Colors
e34197

Requirements
Must have
• Logo, adress, phone contact, e-mail, photo, and our website
Nice to have
• We would like to see a modern business card
Should not have
• Houses or building draws

```html
<!DOCTYPE html>
<html lang="en">
<head>
<meta charset="utf-8">
<title>Lumi Brasa – Business Card</title>
<link href="https://fonts.googleapis.com/css2?family=Arimo:wght@400;700&display=swap" rel="stylesheet">
<style>
  :root {
    --pink: #e34197;
    --white: #ffffff;
    --card-dark: #050505;
    --card-mid: #1e1e1e;
    --backdrop: #cfc8cc;
  }
  * { margin: 0; padding: 0; box-sizing: border-box; }
  html, body {
    width: 1200px; height: 960px; overflow: hidden;
    background: var(--backdrop);
    font-family: "Arimo", Arial, sans-serif;
  }
  .stage {
    width: 1200px; height: 960px;
    display: flex; align-items: center; justify-content: center;
  }
  .card {
    width: 900px; height: 540px;
    background: linear-gradient(115deg, var(--card-mid) 0%, var(--card-dark) 40%, var(--card-dark) 60%, #2a2a2a 100%);
    display: flex; flex-direction: column; align-items: center;
    padding-top: 110px;
    color: var(--white);
  }
  .brand-name {
    color: var(--pink);
    font-weight: 700;
    font-size: 92px;
    line-height: 1;
    letter-spacing: 1px;
  }
  .person { text-align: center; margin-top: 28px; }
  .person-name {
    color: var(--pink); font-weight: 700; font-size: 30px;
    text-transform: uppercase; letter-spacing: 0.5px;
  }
  .person-role {
    font-weight: 700; font-size: 21px; text-transform: uppercase; margin-top: 2px;
  }
  .rule {
    width: 560px; height: 1px; margin: 22px 0;
    background: linear-gradient(90deg, transparent, var(--pink), transparent);
  }
  .contacts { text-align: center; font-size: 21px; line-height: 1.6; }
  .contact-row { display: flex; justify-content: center; align-items: center; gap: 8px; }
  .contact-item { display: inline-flex; align-items: center; gap: 6px; }
  .icon { width: 20px; height: 20px; fill: var(--pink); flex: none; }
</style>
</head>
<body>
<main class="stage">
  <section class="card">
    <h1 class="brand-name">Lumi Brasa</h1>
    <div class="person">
      <p class="person-name">Marco Alves</p>
      <p class="person-role">CEO/Founder</p>
    </div>
    <div class="rule"></div>
    <div class="contacts">
      <p class="address">Rua das Flores Altas, 118, 4400-512, Vila Nova de Gaia</p>
      <p class="contact-row">
        <span class="contact-item">
          <svg class="icon" viewBox="0 0 24 24" aria-hidden="true"><path d="M6.6 10.8a15 15 0 0 0 6.6 6.6l2.2-2.2c.3-.3.7-.4 1-.2 1.1.4 2.3.6 3.6.6.6 0 1 .4 1 1V20c0 .6-.4 1-1 1A17 17 0 0 1 3 4c0-.6.4-1 1-1h3.5c.6 0 1 .4 1 1 0 1.3.2 2.5.6 3.6.1.3 0 .7-.2 1z"/></svg>
          (+351) 220 555 014
        </span>
        <span class="contact-item">
          <svg class="icon" viewBox="0 0 24 24" aria-hidden="true"><path d="M6 3h10l2 2v4H6z M3 10h18v8H3z M7 14h10v7H7z"/></svg>
          (+351) 220 555 019
        </span>
      </p>
      <p class="contact-row">
        <span class="contact-item">
          <svg class="icon" viewBox="0 0 24 24" aria-hidden="true"><path d="M2 5h20v14H2z M2 5l10 8 10-8" stroke="#050505" stroke-width="1.5"/></svg>
          geral@lumibrasa.com
        </span>
        <span class="contact-item">
          <svg class="icon" viewBox="0 0 24 24" aria-hidden="true"><circle cx="12" cy="12" r="10"/><path d="M2 12h20M12 2c3 3 3 17 0 20M12 2c-3 3-3 17 0 20" stroke="#050505" stroke-width="1.4" fill="none"/></svg>
          www.lumibrasa.com
        </span>
      </p>
    </div>
    <div class="rule"></div>
  </section>
</main>
</body>
</html>
```